Elegantes und hochwertiges Etiketten-Design für Weinflasche
Zielgruppe
Wir sind ein liebevoll geführter Familienwinzerbetrieb im schönen Franken, ohne lange Tradition, dafür jung, dynamisch, modern und voller Ideen. Von den eigenen Rebflächen produzieren wir unsere eigenen Weine.
Verantwortlich für den Weinan- und ausbau ist Bernhard, stolzer Familienvater und leidenschaftlicher Hobbywinzer. Unterstützt wird er von seiner Familie, von der Verwandtschaft und von seinen Freunden.
Bernhard ist hauptberuflich Elektroingenieur, Jongleur von Bits und Bytes. Der Ausgleich zum Beruf ist die Arbeit und Ruhe im Weinberg, immer mit dem Drang, etwas Handwerkliches mit den eigenen Händen umzusetzen.
Was hinter dem Weinausbau steckt ist pure Leidenschaft, Passion zur Perfektion, die Liebe zum Wein und das viele Probieren und Tüfteln im Weinberg und im Weinkeller. Und es ist diese Leidenschaft, die uns immer wieder neu motiviert. Dabei haben wir unser Ziel immer fest im Blick, individuelle Weine, Weine die unsere Handschrift tragen und sehr viel Fruchtpotential und Wiedererkennungswert aufweisen, zu erzeugen.
Zielgruppe:
Genussmenschen, die gerne fruchtige, unkomplizierte und mit unserer Handschrift geprägte Weine genießen wollen.
Aufgabenstellung
- Die Weinflasche (vor allem das Etikett) soll im Weinregal positiv ins Auge stechen und die Aufmerksamkeit des Weingenießer auf die Flasche lenken, aber gleichzeitig elegant und hochwertig wirken. Das Etikett soll beim Weingenießer Emotionen wecken und im Gedächtnis bleiben.
- Als Schlagwort soll „Herzensglut“ und die Rebsorte „Bacchus“ auf die Vorderseite des Etiketts gedruckt werden. Das Schlagwort soll dabei im Fokus stehen. „Herzensglut“ steht für die Liebe zwischen mir und meiner Frau, verkörpert in diesem frischen, fruchtigen und lebendigen Bacchus. Da wir dieses Jahr heiraten werden, möchten wir gerne anderen Menschen durch diesen besonderen Wein an unseren „Herzensglut“ teilhaben lassen
- Im Hintergrund des Etiketts soll ein Bild von mir und meiner Frau als schwarz/weiß Kontur abgebildet sein.
- Das Etikett soll später eventuell mit einer Heißfolienprägung veredelt werden (z.B. Folienprägung von Schlagwort „Herzensglut“).
- Das Etikett wird in Digitaldruck auf Selbstklebeetiketten gedruckt.
- Flaschenform: Schlegelflasche antikgrün
- Kapsel: schwarzer BVS-Verschluss

```html
<!DOCTYPE html>
<html lang="de">
<head>
<meta charset="utf-8">
<title>Herzensglut – Bacchus Etikett</title>
<link href="https://fonts.googleapis.com/css2?family=Zilla+Slab:wght@600;700&family=Fira+Sans+Condensed:wght@400;600&family=Nunito+Sans:ital,wght@0,400;0,600;0,700;1,400&display=swap" rel="stylesheet">
<style>
  :root {
    --stage: #f3f3f1;
    --paper: #ffffff;
    --teal: #72c6d3;
    --teal-deep: #5fb6c4;
    --heart: #3a3b3b;
    --gold: #e2a63c;
    --bacchus: #cdb57c;
    --ink: #1c2a30;
    --rule: #b4e1e8;
  }
  * { margin: 0; padding: 0; box-sizing: border-box; }
  html, body { width: 1200px; height: 1112px; overflow: hidden; }
  body { background: var(--stage); position: relative; }

  .label {
    position: absolute; left: 50px; top: 305px;
    width: 1100px; height: 502px;
    background: var(--paper);
    box-shadow: 0 2px 8px rgba(0,0,0,.12);
  }
  .label__panel {
    position: absolute; left: 18px; top: 18px; right: 18px; bottom: 18px;
    background: var(--teal);
    overflow: hidden;
  }
  .couple-art {
    position: absolute; left: 0; top: 12px; width: 390px; height: 454px;
    background: linear-gradient(160deg, var(--teal) 0%, var(--teal-deep) 65%, #9fd6df 100%);
    opacity: .8;
  }
  .sun-rays {
    position: absolute; left: 170px; top: 0; width: 620px; height: 440px;
    background: radial-gradient(ellipse at 50% 40%, rgba(226,166,60,.5) 0%, rgba(226,166,60,.22) 45%, rgba(226,166,60,0) 70%);
  }
  .heart { position: absolute; left: 278px; top: 20px; width: 368px; height: 306px; }
  .title {
    position: absolute; left: 272px; width: 380px; text-align: center;
    font-family: "Zilla Slab", serif; font-weight: 700; color: var(--paper); line-height: 1;
  }
  .title--top { top: 64px; font-size: 66px; letter-spacing: 1px; }
  .title--bottom { top: 140px; font-size: 62px; letter-spacing: 3px; }
  .variety {
    position: absolute; left: 272px; width: 380px; top: 222px; text-align: center;
    font-family: "Zilla Slab", serif; font-weight: 600; font-size: 30px; color: var(--bacchus);
  }
  .story {
    position: absolute; left: 36px; width: 700px; top: 426px; text-align: center;
    font-family: "Fira Sans Condensed", sans-serif; font-size: 17px; line-height: 24px; color: var(--ink);
  }
  .story strong { font-weight: 600; }

  .facts {
    position: absolute; left: 760px; width: 312px; top: 0; height: 100%; text-align: center;
    font-family: "Nunito Sans", sans-serif; color: var(--ink);
  }
  .brand {
    position: absolute; left: 0; right: 0; top: 40px;
    font-weight: 700; font-size: 52px; line-height: 1; color: #111;
    display: flex; align-items: center; justify-content: center; gap: 12px;
  }
  .brand__dot { width: 24px; height: 24px; border-radius: 50%; background: var(--gold); }
  .facts__line { position: absolute; left: 0; right: 0; font-size: 18px; font-weight: 600; }
  .facts__small { position: absolute; left: 0; right: 0; font-size: 14px; }
  .facts__rule { position: absolute; left: 28px; right: 28px; top: 298px; height: 2px; background: var(--rule); }
  .facts__role { position: absolute; left: 0; right: 0; top: 318px; font-size: 16px; font-style: italic; letter-spacing: 1px; }
  .facts__web { color: var(--paper); font-weight: 700; }
  .volume, .alcohol {
    position: absolute; top: 448px; font-family: "Nunito Sans", sans-serif;
    font-size: 22px; font-weight: 600; color: var(--ink);
  }
  .volume { left: 786px; }
  .alcohol { right: 34px; }
</style>
</head>
<body>
  <article class="label">
    <div class="label__panel">
      <div class="couple-art" role="img" aria-label="Konturzeichnung des Brautpaares in Schwarz-Weiß-Linien"></div>
      <div class="sun-rays" role="img" aria-label="Goldene Strahlen rund um das Herz"></div>
    </div>

    <svg class="heart" viewBox="0 0 100 90" preserveAspectRatio="none" aria-hidden="true">
      <path d="M50 88 C20 65 2 48 2 26 C2 10 14 1 27 1 C38 1 46 8 50 16 C54 8 62 1 73 1 C86 1 98 10 98 26 C98 48 80 65 50 88Z" fill="var(--heart)"/>
    </svg>
    <h1 class="title title--top">HERZENS-</h1>
    <div class="title title--bottom">GLUT</div>
    <div class="variety">Bacchus</div>

    <p class="story">
      Ein besonderer Wein anlässlich unserer Hochzeit. <strong>Ein Zeichen unserer Liebe:</strong><br>
      <strong>lebendig, erfrischend, fruchtig.</strong> „Herzensglut“ – dieses Geschenk möchten wir mit Ihnen teilen.
    </p>

    <section class="facts">
      <div class="brand"><span>Sommer</span><span class="brand__dot"></span></div>
      <div class="facts__line" style="top:156px">Franken 2018er</div>
      <div class="facts__line" style="top:179px">Bacchus</div>
      <div class="facts__line" style="top:202px">Q.b.A. feinfruchtig</div>
      <div class="facts__small" style="top:232px;font-size:16px">Deutscher Qualitätswein</div>
      <div class="facts__small" style="top:256px">A.P.Nr. 4210-015-19 – Enthält Sulfite</div>
      <div class="facts__rule"></div>
      <div class="facts__role">– Abfüller –</div>
      <div class="facts__line" style="top:344px;letter-spacing:1px">WEINBAU SOMMER</div>
      <div class="facts__small" style="top:369px;font-size:16px">Lindenweg 7 · D-97999 Rebdorf</div>
      <div class="facts__small" style="top:391px;font-size:16px">Telefon 09999 – 4721</div>
      <div class="facts__small facts__web" style="top:414px;font-size:16px">www.weinbau-sommer.de</div>
    </section>

    <div class="volume">0,75 l</div>
    <div class="alcohol">11,5 % vol</div>
  </article>
</body>
</html>
```